Aquavelo- plumbing service flyer

Hello,
We would like to create flyer for our plumbing company Aquavelo
- we have 2 web domains
aquavelo-example.hr ( official)
preuredjenjedoma-example.hr ( for bathroom renovation)

- we would like to create a similar Z-fold flyer ( from A4 paper) for our services
- We are sending images used on our websites. Of Course, it is allowed to put some of their own. Depending on design
- sending word with text which should go on each page. Text can be modified but in the sense of a page. The massage on a page should be as in word.
What is important to us:
- to stay in blue color
- It should be 1 page when fully open. So it looks like the complete page of information
- first/front page should be with our logo and phone number. more focus on emergency plumbing.
- back page should be about bathroom remodeling. Not necessary but would be received more points
- please don't use images of regular plumbers from Pixelvault and similar. we don't want to use this stock's regular images as all others.

Target Market(s)

Bathroom remodeling and emergency plumbing

Industry/Entity Type

Construction-Plumbing

Colors
0054AA
0677BA
7BADD7
CADEEF
E8F1F8

Requirements
Must have
• Logo

```html
<!DOCTYPE html>
<html lang="hr">
<head>
<meta charset="utf-8">
<title>Aquavelo – plumbing flyer</title>
<link href="https://fonts.googleapis.com/css2?family=Oswald:wght@500;600;700&family=Montserrat:wght@400;500;600;700;800&display=swap" rel="stylesheet">
<style>
:root{
  --blue:#1657ab;
  --blue-deep:#0f4593;
  --blue-bright:#2e8fe3;
  --blue-sky:#7badd7;
  --navy:#182c5c;
  --gold:#f5a71b;
  --paper:#f4f6fa;
  --ink:#1d2f5e;
  --stage:#d8dbe1;
  --head:"Oswald", "Arial Narrow", sans-serif;
  --body:"Montserrat", Arial, sans-serif;
}
*{box-sizing:border-box;margin:0;padding:0}
html,body{width:1200px;height:2358px;overflow:hidden}
body{background:var(--stage);font-family:var(--body);position:relative}
.spread{position:absolute;left:20px;width:1160px;height:820px;overflow:hidden;box-shadow:0 6px 24px rgba(20,30,60,.25)}
.spread--outside{top:330px}
.spread--inside{top:1210px;background:linear-gradient(180deg,var(--blue) 0%,var(--blue-deep) 100%)}
.panel{position:absolute;top:0;width:386.67px;height:820px}
.panel--1{left:0}.panel--2{left:386.67px}.panel--3{left:773.33px}
.overlay{position:absolute;inset:0;width:1160px;height:820px}
.layer{position:absolute;z-index:2}
.hl{color:var(--blue-bright)}
.gold{color:var(--gold)}
.heading{font-family:var(--head);font-weight:600;text-transform:uppercase;letter-spacing:.3px;line-height:1.05}
.rule{width:120px;height:2px;background:var(--gold);margin:10px auto 0}

/* illustration areas */
.art-soft{position:absolute;background:radial-gradient(ellipse at 55% 45%,rgba(140,195,245,.85) 0%,rgba(58,140,225,.7) 35%,rgba(30,95,190,.35) 62%,rgba(22,87,171,0) 78%)}
.art-disc{position:absolute;border-radius:50%;border:4px solid #fff;background:radial-gradient(circle at 50% 38%,#8cc6f5 0%,#3d93e6 45%,#1a5ab8 80%,#14428e 100%);box-shadow:0 4px 14px rgba(10,30,80,.35)}
.art-fade{position:absolute;background:radial-gradient(ellipse at 50% 45%,rgba(123,173,215,.55) 0%,rgba(123,173,215,.25) 50%,rgba(123,173,215,0) 75%)}

/* outside, panel 1 */
.services{background:var(--blue);color:#fff;text-align:center}
.services .heading{font-size:25px;margin-top:22px}
.services .hl{color:#58aef0}
.service-grid{display:grid;grid-template-columns:repeat(3,1fr);row-gap:16px;width:360px;margin:22px auto 0}
.service-grid--two{grid-template-columns:repeat(2,112px);justify-content:center;margin-top:16px}
.service{display:flex;flex-direction:column;align-items:center;font-size:12.5px;font-weight:600;line-height:1.2}
.service svg{display:block}
.service span{margin-top:6px}
.services-foot{position:absolute;left:0;bottom:0;width:386.67px;height:190px;background:var(--paper);border-radius:50% 50% 0 0 / 44px 44px 0 0;text-align:center}
.services-foot .heading{color:var(--blue);font-size:25px;text-transform:none;margin-top:20px}
.foot-row{display:flex;justify-content:space-around;margin-top:20px;padding:0 24px}
.foot-item{display:flex;flex-direction:column;align-items:center;color:var(--ink);font-size:12px;line-height:1.1}
.foot-item b{font-weight:700;font-size:14px;margin-top:4px;letter-spacing:.5px}

/* outside, panel 2 */
.reviews{background:linear-gradient(90deg,#fff 0%,var(--paper) 100%)}
.review{position:relative;margin:24px auto 0;width:338px;border:1.5px solid var(--blue-bright);border-radius:8px;padding:14px 14px 10px;text-align:center;font-size:12.3px;line-height:1.38;color:#3c4560;background:#fff}
.review .stars{position:absolute;top:-9px;left:50%;transform:translateX(-50%);background:#fff;padding:0 6px;display:flex}
.review cite{display:block;font-style:normal;font-weight:700;color:var(--blue);margin-top:4px;letter-spacing:.5px}
.badge-name{position:absolute;left:0;top:462px;width:386.67px;text-align:center;font-family:var(--body);font-weight:700;font-size:17px;color:#fff;letter-spacing:.5px}
.contact{position:absolute;left:0;top:498px;width:386.67px;text-align:center;color:#fff}
.pill{display:inline-block;background:#fff;color:var(--navy);border-radius:20px;padding:3px 20px;font-family:var(--head);font-weight:600;font-size:23px;letter-spacing:.5px}
.contact-line{margin-top:12px;font-size:13px;letter-spacing:1px;line-height:1.3}
.contact-line svg{display:block;margin:0 auto 5px}
.contact-line.phone{font-size:16.5px;font-weight:700;letter-spacing:1.5px}

/* outside, panel 3 */
.cover{background:var(--blue);color:#fff}
.cover-logo{position:absolute;left:24px;top:30px;display:flex;align-items:center;gap:10px;z-index:3}
.cover-logo i{display:block;width:38px;height:38px;border-radius:50%;background:#fff}
.cover-logo span{font-weight:700;font-size:21px;color:#fff}
.cover-copy{position:absolute;left:0;top:500px;width:386.67px;text-align:center}
.cover-copy .heading{font-size:36px}
.cover-copy .hl{color:#5fb4f3}
.cover-copy p{font-size:12.6px;margin-top:18px;line-height:1.5;letter-spacing:.4px;text-transform:uppercase}
.cover-copy p .hl{font-weight:700}
.emergency{display:flex;align-items:center;justify-content:center;gap:8px;margin-top:24px}
.emergency .hours{font-weight:800;font-size:44px;color:#fff;line-height:1;border-left:3px solid var(--gold);border-top:3px solid var(--gold);border-radius:30px 0 0 0;padding:6px 4px 0 8px}
.emergency .words{text-align:left;line-height:1}
.emergency .e1{font-weight:800;font-size:25px;color:var(--gold);letter-spacing:.5px}
.emergency .e2{display:inline-block;margin-top:3px;background:#fff;color:var(--navy);font-weight:800;font-size:16px;padding:3px 10px;letter-spacing:1px}
.phone-pill{display:inline-flex;align-items:center;gap:8px;margin-top:18px;background:var(--gold);color:var(--navy);border-radius:22px;padding:4px 16px 4px 6px;font-weight:800;font-size:21px;letter-spacing:1px}
.phone-pill i,.blue-pill i{display:flex;width:28px;height:28px;border-radius:50%;background:#fff;align-items:center;justify-content:center}

/* inside */
.inside-title{position:absolute;top:24px;width:1160px;text-align:center;color:#fff;font-size:27px;z-index:2}
.column{position:absolute;top:82px;width:386.67px;padding:0 25px;color:#fff;z-index:2}
.column .heading{font-size:18px;text-align:center}
.column .hl{color:#5fb4f3}
.column p{margin-top:12px;font-size:12.6px;line-height:1.36;color:#e4ecf7}
.col-1{left:0}.col-2{left:386.67px}.col-3{left:773.33px}
.tail{position:absolute;z-index:5;color:var(--ink)}
.tail .heading{font-size:23px;color:var(--blue);text-align:center;white-space:nowrap}
.checklist{list-style:none}
.checklist li{display:flex;align-items:center;gap:12px;font-size:14px;font-weight:500;margin-bottom:13px;color:#2a355a}
.checklist li i{display:block;width:28px;height:28px;border-radius:50%;background:var(--gold);border:3px solid #fbd48a;flex:none}
.tail-cta{text-align:center;font-size:13.5px;letter-spacing:.8px;margin-top:12px}
.tail-cta .gold{font-weight:700}
.blue-pill{display:inline-flex;align-items:center;gap:8px;margin-top:8px;background:var(--blue-bright);color:#fff;border-radius:22px;padding:4px 18px 4px 6px;font-weight:800;font-size:21px;letter-spacing:1px}
.site{margin-top:10px;font-size:12.5px;letter-spacing:.8px;text-align:center}
.site b{font-weight:700}
</style>
</head>
<body>

<section class="spread spread--outside" aria-label="Flyer outside">
  <div class="panel panel--1 services">
    <h2 class="heading">Our full range of <span class="hl">plumbing</span><br>services</h2>
    <div class="rule"></div>
    <div class="service-grid">
      <div class="service"><svg width="36" height="46" viewBox="0 0 36 46"><circle cx="18" cy="18" r="17" fill="#fff"/><path d="M18 9c4 6 6 9 6 12a6 6 0 0 1-12 0c0-3 2-6 6-12z" fill="none" stroke="#1657ab" stroke-width="1.6"/><path d="M12 39h12l-6 6z" fill="#f5a71b"/></svg><span>Leak<br>Detection</span></div>
      <div class="service"><svg width="36" height="46" viewBox="0 0 36 46"><circle cx="18" cy="18" r="17" fill="#fff"/><path d="M12 9h12v7H12zM11 18h14c0 5-3 8-7 8s-7-3-7-8z" fill="none" stroke="#1657ab" stroke-width="1.6"/><path d="M12 39h12l-6 6z" fill="#f5a71b"/></svg><span>Toilet Repair<br>&amp; Installation</span></div>
      <div class="service"><svg width="36" height="46" viewBox="0 0 36 46"><circle cx="18" cy="18" r="17" fill="#fff"/><path d="M8 22h20M8 16h20M12 12v14M24 12v14" fill="none" stroke="#1657ab" stroke-width="1.6"/><path d="M12 39h12l-6 6z" fill="#f5a71b"/></svg><span>Gas<br>Lines</span></div>
      <div class="service"><svg width="36" height="46" viewBox="0 0 36 46"><circle cx="18" cy="18" r="17" fill="#fff"/><path d="M14 9v12a4 4 0 0 0 8 0v-4M19 13h6" fill="none" stroke="#1657ab" stroke-width="1.6"/><path d="M12 39h12l-6 6z" fill="#f5a71b"/></svg><span>Drain<br>Cleaning</span></div>
      <div class="service"><svg width="36" height="46" viewBox="0 0 36 46"><circle cx="18" cy="18" r="17" fill="#fff"/><path d="M9 18h18M18 10v8M14 10h8M13 15v6M23 15v6" fill="none" stroke="#1657ab" stroke-width="1.6"/><path d="M12 39h12l-6 6z" fill="#f5a71b"/></svg><span>Gas<br>Valves</span></div>
      <div class="service"><svg width="36" height="46" viewBox="0 0 36 46"><circle cx="18" cy="18" r="17" fill="#fff"/><path d="M12 9v8h12V9M18 17v10" fill="none" stroke="#1657ab" stroke-width="1.6"/><path d="M12 39h12l-6 6z" fill="#f5a71b"/></svg><span>Drain<br>Repair</span></div>
      <div class="service"><svg width="36" height="46" viewBox="0 0 36 46"><circle cx="18" cy="18" r="17" fill="#fff"/><path d="M9 18h18a9 6 0 0 1-18 0zM12 18V10h5" fill="none" stroke="#1657ab" stroke-width="1.6"/><path d="M12 39h12l-6 6z" fill="#f5a71b"/></svg><span>Shower Repair<br>&amp; Installation</span></div>
      <div class="service"><svg width="36" height="46" viewBox="0 0 36 46"><circle cx="18" cy="18" r="17" fill="#fff"/><path d="M8 15h20v6H8zM18 23c2 3 2 4 0 5-2-1-2-2 0-5z" fill="none" stroke="#1657ab" stroke-width="1.6"/><path d="M12 39h12l-6 6z" fill="#f5a71b"/></svg><span>Burst<br>Pipes</span></div>
      <div class="service"><svg width="36" height="46" viewBox="0 0 36 46"><circle cx="18" cy="18" r="17" fill="#fff"/><path d="M9 24h18M13 24v-8h10v8M18 16v-5" fill="none" stroke="#1657ab" stroke-width="1.6"/><path d="M12 39h12l-6 6z" fill="#f5a71b"/></svg><span>Rooter<br>Services</span></div>
      <div class="service"><svg width="36" height="46" viewBox="0 0 36 46"><circle cx="18" cy="18" r="17" fill="#fff"/><path d="M10 25l4-12h8l4 12zM13 19h10" fill="none" stroke="#1657ab" stroke-width="1.6"/><path d="M12 39h12l-6 6z" fill="#f5a71b"/></svg><span>Garbage<br>Disposals</span></div>
      <div class="service"><svg width="36" height="46" viewBox="0 0 36 46"><circle cx="18" cy="18" r="17" fill="#fff"/><path d="M11 25l10-10M20 11a4 4 0 1 0 5 5" fill="none" stroke="#1657ab" stroke-width="1.8"/><path d="M12 39h12l-6 6z" fill="#f5a71b"/></svg><span>Pipe<br>Repair</span></div>
      <div class="service"><svg width="36" height="46" viewBox="0 0 36 46"><circle cx="18" cy="18" r="17" fill="#fff"/><path d="M11 11l14 14M25 11L11 25" fill="none" stroke="#1657ab" stroke-width="1.8"/><path d="M12 39h12l-6 6z" fill="#f5a71b"/></svg><span>Plumbing<br>Repairs</span></div>
    </div>
    <div class="service-grid service-grid--two">
      <div class="service"><svg width="36" height="46" viewBox="0 0 36 46"><circle cx="18" cy="18" r="17" fill="#fff"/><rect x="12" y="9" width="12" height="18" rx="2" fill="none" stroke="#1657ab" stroke-width="1.6"/><circle cx="18" cy="19" r="3" fill="none" stroke="#1657ab" stroke-width="1.4"/><path d="M12 39h12l-6 6z" fill="#f5a71b"/></svg><span>Water Heaters</span></div>
      <div class="service"><svg width="36" height="46" viewBox="0 0 36 46"><circle cx="18" cy="18" r="17" fill="#fff"/><path d="M9 14h18M9 22h18M13 10v16M23 10v16" fill="none" stroke="#1657ab" stroke-width="1.6"/><path d="M12 39h12l-6 6z" fill="#f5a71b"/></svg><span>Pipelining</span></div>
    </div>
    <div class="services-foot">
      <h3 class="heading">Aquavelo Services</h3>
      <div class="foot-row">
        <div class="foot-item"><svg width="30" height="38" viewBox="0 0 30 38"><circle cx="15" cy="15" r="14" fill="#1657ab"/><path d="M10 9v9a5 5 0 0 0 10 0" fill="none" stroke="#fff" stroke-width="1.6"/><path d="M10 32h10l-5 5z" fill="#f5a71b"/></svg><b>DRAIN</b>Cleaning</div>
        <div class="foot-item"><svg width="30" height="38" viewBox="0 0 30 38"><circle cx="15" cy="15" r="14" fill="#1657ab"/><path d="M9 21l9-9M17 8a4 4 0 1 0 5 5" fill="none" stroke="#fff" stroke-width="1.6"/><path d="M10 32h10l-5 5z" fill="#f5a71b"/></svg><b>PLUMBING</b>Services</div>
        <div class="foot-item"><svg width="30" height="38" viewBox="0 0 30 38"><circle cx="15" cy="15" r="14" fill="#1657ab"/><path d="M15 7c4 5 5 8 5 10a5 5 0 0 1-10 0c0-2 1-5 5-10z" fill="none" stroke="#fff" stroke-width="1.6"/><path d="M10 32h10l-5 5z" fill="#f5a71b"/></svg><b>LEAK</b>Detection</div>
      </div>
    </div>
  </div>

  <div class="panel panel--2 reviews"></div>
  <div class="panel panel--3 cover">
    <div class="art-soft" style="left:20px;top:20px;width:380px;height:430px" role="img" aria-label="Illustration of the masked plumbing hero mascot carrying a pipe on his shoulder and giving a thumbs up"></div>
  </div>

  <svg class="overlay" viewBox="0 0 1160 820" aria-hidden="true">
    <path d="M386.67 460 Q 580 470 773.33 445 L773.33 820 L386.67 820Z" fill="#182c5c"/>
    <path d="M773.33 445 Q 980 420 1160 340 L1160 820 L773.33 820Z" fill="#1657ab"/>
    <path d="M350 450 Q 600 476 820 438 Q 1000 405 1160 330" fill="none" stroke="#f5a71b" stroke-width="9"/>
    <path d="M773.33 452 Q 1000 420 1160 350" fill="none" stroke="#1a4a94" stroke-width="6"/>
  </svg>

  <div class="layer" style="left:386.67px;top:0;width:386.67px;height:820px">
    <h2 class="heading" style="color:var(--blue);font-size:25px;text-align:center;margin-top:22px">Customer review</h2>
    <div class="rule"></div>
    <div class="review">
      <span class="stars"><svg width="80" height="14" viewBox="0 0 80 14"><defs><path id="st" d="M7 0l2 5h5l-4 3 2 5-5-3-5 3 2-5-4-3h5z"/></defs><g fill="#f5a71b"><use href="#st"/><use href="#st" x="16"/><use href="#st" x="32"/><use href="#st" x="48"/><use href="#st" x="64"/></g></svg></span>
      Momci su bili profesionalni i odradili posao bez greske. Kombi opremljen sa hrpom alata. I najvaznije dosli u dogovoreno vrijeme. Za svaku preporuku
      <cite>Tomislav R.</cite>
    </div>
    <div class="review">
      <span class="stars"><svg width="80" height="14" viewBox="0 0 80 14"><g fill="#f5a71b"><use href="#st"/><use href="#st" x="16"/><use href="#st" x="32"/><use href="#st" x="48"/><use href="#st" x="64"/></g></svg></span>
      Bilo nam je potrebno snimanje kanalizacije s kojom vec neko vrijeme imamo problema. Snimili su cijev i tocno odredili njezinu putanju za laksu sanaciju. Za svaku pohvalu.
      <cite>Luka P.</cite>
    </div>
    <div class="art-disc" style="left:139px;top:340px;width:108px;height:108px" role="img" aria-label="Round badge with the plumbing hero mascot"></div>
    <div class="badge-name">Aquavelo</div>
    <div class="contact">
      <span class="pill">CONTACT US</span>
      <div class="contact-line phone"><svg width="22" height="22" viewBox="0 0 22 22"><circle cx="11" cy="11" r="10" fill="#f5a71b"/><path d="M7.5 6.5l2 0 1 2.5-1.3 1a6 6 0 0 0 2.8 2.8l1-1.3 2.5 1v2a1 1 0 0 1-1 1A8 8 0 0 1 6.5 7.5a1 1 0 0 1 1-1z" fill="#fff"/></svg>091 400 1234</div>
      <div class="contact-line"><svg width="22" height="22" viewBox="0 0 22 22"><circle cx="11" cy="11" r="10" fill="#f5a71b"/><rect x="6" y="7.5" width="10" height="7" fill="none" stroke="#fff" stroke-width="1.3"/><path d="M6 7.5l5 4 5-4" fill="none" stroke="#fff" stroke-width="1.3"/></svg>info@<b>aquavelo-example</b>.hr</div>
      <div class="contact-line"><svg width="22" height="22" viewBox="0 0 22 22"><circle cx="11" cy="11" r="10" fill="#f5a71b"/><circle cx="11" cy="11" r="5.5" fill="none" stroke="#fff" stroke-width="1.3"/><path d="M5.5 11h11M11 5.5c-2.5 3-2.5 8 0 11M11 5.5c2.5 3 2.5 8 0 11" fill="none" stroke="#fff" stroke-width="1.1"/></svg>www.<b>aquavelo-example</b>.hr</div>
      <div class="contact-line"><svg width="22" height="22" viewBox="0 0 22 22"><circle cx="11" cy="11" r="10" fill="#f5a71b"/><path d="M11 16.5s-4-4-4-7a4 4 0 0 1 8 0c0 3-4 7-4 7z" fill="none" stroke="#fff" stroke-width="1.3"/><circle cx="11" cy="9.5" r="1.4" fill="#fff"/></svg>45 Harbour Lane, Riverton,<br>State, 54321</div>
    </div>
  </div>

  <div class="layer" style="left:773.33px;top:0;width:386.67px;height:820px;color:#fff">
    <div class="cover-logo"><i></i><span>Aquavelo</span></div>
    <div class="cover-copy">
      <h1 class="heading">Let the water <span class="hl">stay in<br>the pipes</span> only.</h1>
      <p>We’re open <span class="hl">24/7/365</span> because<br>plumbing emergencies don’t wait ...</p>
      <div class="emergency">
        <span class="hours">24</span>
        <span class="words"><span class="e1">EMERGENCY</span><br><span class="e2">PLUMBING</span></span>
      </div>
      <span class="phone-pill"><i><svg width="16" height="16" viewBox="0 0 22 22"><path d="M6 4l3 0 1.5 3.5-2 1.5a8 8 0 0 0 4.5 4.5l1.5-2L18 13v3a1.5 1.5 0 0 1-1.5 1.5A13 13 0 0 1 4.5 5.5 1.5 1.5 0 0 1 6 4z" fill="#182c5c"/></svg></i>095 300 2211</span>
    </div>
  </div>
</section>

<section class="spread spread--inside" aria-label="Flyer inside">
  <h2 class="heading inside-title">Premier plumbing in your area</h2>

  <div class="column col-1">
    <h3 class="heading">Professional plumbing <span class="hl">services</span></h3>
    <p>Lorem Ipsum is simply dummy text of the printing and typesetting industry. Lorem Ipsum has been the industry's standard dummy text ever since the 1500s, when an unknown printer took a galley of type and scrambled it to make a type specimen book. It has survived not only five centuries, but also the leap into electronic typesetting, remaining essentially unchanged. It was popularised in the 1960s with the release of Letraset sheets containing Lorem Ipsum passages, and more recently with desktop publishing software like Aldus PageMaker including versions of Lorem Ipsum. Lorem Ipsum is simply dummy text of the printing and typesetting industry. It was popularised in the 1960s with the release of Letraset sheets containing Lorem Ipsum passages, and more recently with desktop publishing software like Aldus PageMaker including versions of Lorem Ipsum.</p>
  </div>
  <div class="column col-2">
    <h3 class="heading">Professional drain <span class="hl">services</span></h3>
    <p>Lorem Ipsum is simply dummy text of the printing and typesetting industry. Lorem Ipsum has been the industry's standard dummy text ever since the 1500s, when an unknown printer took a galley of type and scrambled it to make a type specimen book. It has survived not only five centuries, but also the leap into electronic typesetting, remaining essentially unchanged. It was popularised in the 1960s with the release of Letraset sheets containing Lorem Ipsum passages, and more recently with desktop publishing software like Aldus PageMaker including versions of Lorem Ipsum. Lorem Ipsum is simply dummy text of the printing and typesetting industry. It was popularised in the 1960s with the release of Letraset sheets containing Lorem Ipsum passages, and more recently with desktop publishing software like Aldus PageMaker including versions of Lorem Ipsum.</p>
  </div>
  <div class="column col-3">
    <h3 class="heading">Professional rocket <span class="hl">services</span></h3>
    <p>Lorem Ipsum is simply dummy text of the printing and typesetting industry. Lorem Ipsum has been the industry's standard dummy text ever since the 1500s, when an unknown printer took a galley of type and scrambled it to make a type specimen book. It has survived not only five centuries, but also the leap into electronic typesetting, remaining essentially unchanged. It was popularised in the 1960s with the release of Letraset sheets containing Lorem Ipsum passages, and more recently with desktop publishing software like Aldus PageMaker including versions of Lorem Ipsum. Lorem Ipsum is simply dummy text of the printing and typesetting industry. It was popularised in the 1960s with the release of Letraset sheets containing Lorem Ipsum passages, and more recently with desktop publishing software like Aldus PageMaker including versions of Lorem Ipsum.</p>
  </div>

  <svg class="overlay" viewBox="0 0 1160 820" aria-hidden="true" style="z-index:2">
    <path d="M0 660 Q 280 560 580 548 Q 880 548 1160 640 L1160 820 L0 820Z" fill="#f4f6fa"/>
    <path d="M0 650 Q 280 548 580 538 Q 880 538 1160 630" fill="none" stroke="#f5a71b" stroke-width="8"/>
  </svg>

  <div class="art-disc" style="left:118px;top:468px;width:150px;height:150px;z-index:3" role="img" aria-label="Mascot illustration of the plumbing hero standing with a wrench"></div>
  <div class="art-disc" style="left:505px;top:468px;width:150px;height:150px;z-index:3" role="img" aria-label="Mascot illustration of the plumbing hero standing with a pipe"></div>
  <div class="art-disc" style="left:900px;top:462px;width:150px;height:150px;z-index:3" role="img" aria-label="Mascot illustration of the plumbing hero flying with a thumbs up"></div>

  <div class="art-fade" style="left:220px;top:700px;width:160px;height:120px;z-index:3" role="img" aria-label="Faded mascot illustration of the plumbing hero"></div>
  <div class="art-soft" style="left:570px;top:650px;width:240px;height:190px;z-index:3" role="img" aria-label="Mascot illustration of the plumbing hero with a pipe on his shoulder"></div>

  <div class="tail" style="left:25px;top:666px;width:340px">
    <h3 class="heading">Count on us for plumbing</h3>
    <div class="rule" style="margin-top:6px"></div>
    <ul class="checklist" style="margin-top:16px">
      <li><i></i>24/7 Emergency</li>
      <li><i></i>Installations</li>
    </ul>
  </div>
  <div class="tail" style="left:411px;top:686px;width:190px">
    <ul class="checklist">
      <li><i></i>Repairs</li>
      <li><i></i>Replacements</li>
      <li><i></i>Maintenance</li>
    </ul>
  </div>
  <div class="tail" style="left:773.33px;top:666px;width:386.67px">
    <h3 class="heading">Using tech to facilitate your life</h3>
    <div class="tail-cta">CONTACT OUR <span class="gold">EXPERTS</span> NOW</div>
    <div style="text-align:center"><span class="blue-pill"><i><svg width="16" height="16" viewBox="0 0 22 22"><path d="M6 4l3 0 1.5 3.5-2 1.5a8 8 0 0 0 4.5 4.5l1.5-2L18 13v3a1.5 1.5 0 0 1-1.5 1.5A13 13 0 0 1 4.5 5.5 1.5 1.5 0 0 1 6 4z" fill="#2e8fe3"/></svg></i>095 300 7788</span></div>
    <div class="site">www.<b>preuredjenjedoma-example</b>.hr</div>
  </div>
</section>

</body>
</html>
```